Beacon Advisory Website

I currently have a website www.beaconadvisoryinc.com. We are a IT Consulting Company. Our website will pretty much tell out our services. I am looking to enhance my website and make it look more professional. Looking for very classy and Contemporary look and design for my website.

It Company

```html
<!DOCTYPE html>
<html lang="en">
<head>
<meta charset="utf-8">
<title>Beacon Advisory</title>
<link rel="stylesheet" href="https://fonts.googleapis.com/css2?family=Source+Sans+3:wght@300;400;600;700&display=swap">
<style>
:root{
  --brand:#1667b0;
  --brand-dark:#1b5c9f;
  --sky:#0a93d4;
  --accent:#0b8fd0;
  --ink:#333;
  --muted:#666;
  --light:#f5f5f5;
  --footer:#f1f1f1;
  --white:#fff;
}
*{margin:0;padding:0;box-sizing:border-box}
html,body{width:1200px;height:2647px;overflow:hidden}
body{font-family:"Source Sans 3",sans-serif;color:var(--ink);background:var(--white)}
.site-header{height:106px;position:relative;background:var(--white)}
.brand{position:absolute;left:115px;top:34px;display:flex;align-items:center;gap:10px;font-weight:700;font-size:26px;color:var(--brand);letter-spacing:.5px}
.brand-mark{width:30px;height:30px;border-radius:50%;background:var(--brand)}
.main-nav{position:absolute;top:63px;left:0;width:100%}
.main-nav a{position:absolute;font-size:14px;font-weight:600;color:#222;text-decoration:none;letter-spacing:.3px}
.hero{position:relative;height:499px;background:linear-gradient(100deg,#1f8ad8 0%,#1a6fc4 45%,#0f4f9a 75%,#0b3470 100%);color:var(--white)}
.hero-art{position:absolute;left:0;top:0;width:100%;height:100%}
.hero-title{position:absolute;left:141px;top:308px;font-size:37px;font-weight:400;letter-spacing:.5px}
.hero-text{position:absolute;left:146px;top:362px;width:400px;font-size:14px;line-height:22px;opacity:.92}
.btn-solid{position:absolute;left:147px;top:450px;width:139px;height:46px;background:#0d3b7a;color:var(--white);font-size:14px;font-weight:600;display:flex;align-items:center;justify-content:center;text-decoration:none}
.dots{position:absolute;display:flex;gap:9px}
.dots span{width:9px;height:9px;border-radius:50%}
.hero .dots{left:571px;top:566px}
.hero .dots span{background:rgba(255,255,255,.5)}
.hero .dots span.on{background:var(--white)}
.welcome{position:relative;height:339px;background:var(--light);text-align:center}
.welcome-deco{position:absolute;left:0;top:20px;width:250px;height:230px}
.section-title{font-size:23px;font-weight:600;color:var(--accent);letter-spacing:.3px}
.welcome .section-title{position:absolute;left:0;right:0;top:56px}
.welcome p{position:absolute;left:170px;width:860px;top:130px;font-size:14px;line-height:24px;color:var(--muted)}
.btn-outline{position:absolute;left:545px;top:265px;width:111px;height:39px;border:1px solid #777;color:var(--brand);font-size:13px;font-weight:700;display:flex;align-items:center;justify-content:center;text-decoration:none;background:var(--white)}
.services{position:relative;height:441px;background:var(--white)}
.services .section-title{position:absolute;left:0;right:0;top:64px;text-align:center;color:var(--brand-dark)}
.service{position:absolute;top:155px;width:288px}
.service-head{display:flex;align-items:center;gap:10px;height:64px;border-bottom:3px solid var(--brand)}
.service-icon{width:62px;height:62px;border-radius:50%;background:var(--accent);display:flex;align-items:center;justify-content:center}
.service-name{font-size:20px;color:#333;letter-spacing:.3px}
.service p{margin-top:24px;font-size:11.5px;line-height:19px;color:#555}
.services .dots{left:566px;top:1344px;position:absolute}
.services .dots{top:400px}
.services .dots span{background:#ccc}
.services .dots span.on{background:var(--accent)}
.feature{position:relative;height:355px}
.feature-dark{background:var(--brand-dark);color:var(--white)}
.feature-light{background:var(--white);height:353px}
.feature-sky{background:var(--sky);color:var(--white)}
.photo{position:absolute;width:310px;height:310px;border-radius:50%;border:5px solid var(--white);box-shadow:0 4px 14px rgba(0,0,0,.25)}
.feature h2{position:absolute;font-size:23px;font-weight:600;letter-spacing:.5px}
.feature p{font-size:14px;line-height:24px}
.feature .copy{position:absolute}
.feature-light h2{color:var(--brand-dark)}
.feature-light p{color:var(--muted)}
.site-footer{position:relative;height:199px;background:var(--footer);text-align:center}
.site-footer .brand{position:absolute;left:50%;top:36px;transform:translateX(-50%)}
.footer-nav{position:absolute;left:0;right:0;top:101px;display:flex;justify-content:center;gap:0;font-size:13px;font-weight:600}
.footer-nav a{color:#222;text-decoration:none;padding:0 26px;border-left:1px solid #444}
.footer-nav a:first-child{border-left:none}
.copyright{position:absolute;left:0;right:0;top:140px;font-size:13px;font-weight:600;color:#333}
</style>
</head>
<body>
<header class="site-header">
  <div class="brand"><span class="brand-mark"></span>Beacon Advisory</div>
  <nav class="main-nav">
    <a style="left:415px">COMPANY</a>
    <a style="left:521px">SERVICES</a>
    <a style="left:626px">SOLUTIONS</a>
    <a style="left:743px">RESOURCES</a>
    <a style="left:863px">CAREER</a>
    <a style="left:956px">CONTACT US</a>
  </nav>
</header>

<section class="hero">
  <div class="hero-art" role="img" aria-label="Businessman in a suit touching a glowing network of blue gears"></div>
  <h1 class="hero-title">BEACON ADVISORY</h1>
  <p class="hero-text">Sed ut perspiciatis unde omnis iste natus error sit voluptatem accusantium doloremque laudantium, totam rem aperiam, eaque ipsa quae ab illo inventore veritatis et quasi architecto</p>
  <a class="btn-solid">LEARN MORE</a>
  <div class="dots"><span></span><span class="on"></span><span class="on"></span><span class="on"></span></div>
</section>

<section class="welcome">
  <svg class="welcome-deco" viewBox="0 0 250 230" aria-hidden="true"><circle cx="60" cy="115" r="120" fill="#e6eef6"/></svg>
  <h2 class="section-title">WELCOME TO BEACON ADVISORY</h2>
  <p>Today's IT market is a dynamic, fast-paced industry, with ever-increasing demands. Meeting these demands for over 25 years, Beacon Advisory maintains a global presence, aggressively recruiting expertly qualified IT and Management Professionals from around the world and cultivating key partnerships with corporations to understand their business models end-to-end, with a goal of delivering exceptional client service and ensuring a consistent delivery of the talent needed to drive results</p>
  <a class="btn-outline">LEARN MORE</a>
</section>

<section class="services">
  <h2 class="section-title">OUR SERVICES</h2>
  <div class="service" style="left:145px">
    <div class="service-head">
      <span class="service-icon"><svg width="30" height="30" viewBox="0 0 30 30"><rect x="4" y="20" width="4" height="6" fill="#fff"/><rect x="10" y="15" width="4" height="11" fill="#fff"/><rect x="16" y="10" width="4" height="16" fill="#fff"/><rect x="22" y="5" width="4" height="21" fill="#fff"/></svg></span>
      <span class="service-name">BUSINESS</span>
    </div>
    <p>Lorem Ipsum is simply dummy text of the printing and typesetting industry. Lorem Ipsum has been the industry's standard dummy text ever since the 1500s, when an unknown printer took a galley of type and scrambled it to make a type specimen book.</p>
  </div>
  <div class="service" style="left:454px">
    <div class="service-head">
      <span class="service-icon"><svg width="30" height="30" viewBox="0 0 30 30"><path d="M15 3a8 8 0 0 0-5 14v4h10v-4a8 8 0 0 0-5-14z" fill="none" stroke="#fff" stroke-width="2.5"/><rect x="11" y="23" width="8" height="3" fill="#fff"/></svg></span>
      <span class="service-name">TECHNOLOGY</span>
    </div>
    <p>Lorem Ipsum is simply dummy text of the printing and typesetting industry. Lorem Ipsum has been the industry's standard dummy text ever since the 1500s, when an unknown printer took a galley of type and scrambled it to make a type specimen book.</p>
  </div>
  <div class="service" style="left:768px">
    <div class="service-head">
      <span class="service-icon"><svg width="30" height="30" viewBox="0 0 30 30"><rect x="4" y="6" width="19" height="19" rx="3" fill="none" stroke="#fff" stroke-width="2.5"/><path d="M12 19l2-6 11-11 4 4-11 11z" fill="#fff"/></svg></span>
      <span class="service-name">APPLICATION</span>
    </div>
    <p>Lorem Ipsum is simply dummy text of the printing and typesetting industry. Lorem Ipsum has been the industry's standard dummy text ever since the 1500s, when an unknown printer took a galley of type and scrambled it to make a type specimen book.</p>
  </div>
  <div class="dots"><span class="on"></span><span></span><span></span><span></span></div>
</section>

<section class="feature feature-dark">
  <div class="photo" role="img" aria-label="Team working together at laptops in a bright office" style="left:142px;top:22px;background:linear-gradient(160deg,#d9e2ea,#8fa3b5 60%,#4f6a3e)"></div>
  <h2 style="left:535px;top:46px">IT CONSULTING</h2>
  <div class="copy" style="left:535px;top:110px;width:510px">
    <p>Information technology should improve business results. Beacon helps companies make sure it does. We look at IT issues strategically, in the broader context of our clients' business. Our experts provide an objective, independent perspective to help companies realize the full potential of their IT resources, investments and assets.</p>
    <p style="margin-top:24px">We draw on global experience across industries and technologies to help solve companies' most complex IT challenges. More than 40% of our work is done in the context of major transformation in the business or in IT.</p>
  </div>
</section>

<section class="feature feature-light">
  <h2 style="left:143px;top:60px">STAFF AUGMENTATION</h2>
  <div class="copy" style="left:143px;top:120px;width:515px">
    <p>For years Beacon Advisory has been offering our customers the ability to augment their existing staff with temporary highly skilled IT professionals who can help address immediate short term needs. We know that often our customers have brief spikes in their need for reporting, for example. With internal IT teams focused on more strategic projects, it can be difficult to justify diverting a team member for a few weeks to relieve this short term pressure from business users. This is an ideal situation in which to consider bringing in one of our team.</p>
  </div>
  <div class="photo" role="img" aria-label="Silhouettes of business people standing before a glass office tower" style="left:749px;top:23px;background:linear-gradient(180deg,#e9f1f8,#8fb0d2 55%,#2a3f5c)"></div>
</section>

<section class="feature feature-sky">
  <div class="photo" role="img" aria-label="Businessman at a desk reviewing documents" style="left:142px;top:28px;background:linear-gradient(160deg,#f0ede8,#c9bfb2 55%,#8a7a68)"></div>
  <h2 style="left:535px;top:93px">OFFSHORE</h2>
  <div class="copy" style="left:535px;top:150px;width:510px">
    <p>Our Offshore development model has a unique distinction of providing efficient software solutions with cost and quality advantage, using state-of-the-art technologies, having the capacity to handle large projects and, above all, the ability to execute timely deliveries.</p>
  </div>
</section>

<footer class="site-footer">
  <div class="brand"><span class="brand-mark"></span>Beacon Advisory</div>
  <nav class="footer-nav">
    <a>COMPANY</a><a>SERVICES</a><a>SOLUTIONS</a><a>RESOURCES</a><a>CAREER</a><a>CONTACT US</a>
  </nav>
  <p class="copyright">© 2016 COMPANY NAME | ALL RIGHTS RESERVED</p>
</footer>
</body>
</html>
```